New Mechanical Maintenance business needs website

New Mechanical Maintenance business in Perth Western Australia needs a nice and easy to navigate website. Showing what we do and how we can be the right fit for other small to medium size business by offering personalized service from our highly skilled team. We deal with both fixed plant repairs like food and chemical processing facilities to heavy equipment like drill rigs, Large boats and earthmoving equipment.

Target Market(s)

Small to medium business to offer personalized services/packages

Industry/Entity Type

e deal with both fixed plant repairs like food and chemical processing facilities to heavy equipment like drill rigs, Large boats and earthmoving equipment.

Coding

Coded - Design and coding required

Number of Pages Required

4 page

Font styles to use
Serif

Colors
0054AA
0677BA
7BADD7
CADEEF
E8F1F8

Requirements
Must have
• A website that is easy to navigate but covers off on the range of services/maintenance we can provide

```html
<!DOCTYPE html>
<html lang="en">
<head>
<meta charset="utf-8">
<title>KVR Maintenance — Mechanical Maintenance</title>
<link href="https://fonts.googleapis.com/css2?family=Poppins:wght@500;600;700&family=Lato:wght@400;700&display=swap" rel="stylesheet">
<style>
:root{
  --blue-deep:#0054AA;
  --blue:#0677BA;
  --blue-soft:#7BADD7;
  --blue-pale:#CADEEF;
  --blue-mist:#E8F1F8;
  --slate:#4E5D7E;
  --slate-dark:#5A6371;
  --ink:#222;
  --black:#0b0b0b;
  --white:#fff;
}
*{margin:0;padding:0;box-sizing:border-box}
html,body{width:1200px;height:3393px;overflow:hidden;background:var(--white)}
body{position:relative;font-family:'Lato',sans-serif;color:var(--ink)}
.abs{position:absolute}
.head{font-family:'Poppins',sans-serif;font-weight:700}

.topbar{left:0;top:0;width:1200px;height:51px;background:#5b5b5b;color:var(--white);font-size:14px;font-weight:700;display:flex;align-items:center;justify-content:center}
.hero{left:0;top:51px;width:1200px;height:633px;background:linear-gradient(90deg,#1a1a1a 0%,#2a2a2c 35%,#4a4d52 60%,#3a3a3c 100%)}
.brand{display:flex;align-items:center;gap:10px;color:var(--white);font-family:'Poppins',sans-serif;font-weight:600;font-size:17px;line-height:1.1}
.brand .mark{width:46px;height:46px;border-radius:50%;border:4px solid var(--white)}
.nav{top:117px;left:294px;display:flex;gap:48px;color:var(--white);font-family:'Poppins',sans-serif;font-weight:600;font-size:15px}
.socials{top:119px;left:814px;display:flex;gap:24px}
.socials span{width:16px;height:16px;border-radius:50%;background:var(--white);display:block}
.btn{display:flex;align-items:center;justify-content:center;border-radius:30px;font-family:'Poppins',sans-serif;font-weight:600}
.btn-contact{left:990px;top:106px;width:186px;height:42px;background:var(--white);color:#333;font-size:15px}
.hero-kicker{left:111px;top:272px;color:var(--white);font-family:'Poppins',sans-serif;font-weight:600;font-size:15px;letter-spacing:4px}
.hero-title{left:108px;top:302px;color:var(--white);font-size:37px;line-height:52px;letter-spacing:.5px}
.hero-text{left:111px;top:418px;width:430px;color:var(--white);font-size:15px;line-height:31px}
.btn-start{left:111px;top:532px;width:165px;height:46px;background:var(--white);color:#444;font-size:15px}
.hero-tel{left:313px;top:536px;color:var(--white);font-size:27px}

.why-art{left:110px;top:745px;width:445px;height:468px}
.why-title{left:624px;top:780px;color:var(--slate);font-size:35px}
.why-text{left:624px;top:838px;width:465px;font-size:15px;line-height:29px;text-align:justify;color:#333}
.why-text p+p{margin-top:29px}
.btn-dark{left:624px;top:1113px;width:158px;height:47px;background:var(--slate-dark);color:var(--white);font-size:16px;box-shadow:0 2px 6px rgba(0,0,0,.25)}

.services-band{left:0;top:1240px;width:1200px;height:890px}
.services-title{left:0;top:1340px;width:1200px;text-align:center;color:var(--white);font-size:34px}
.card{width:314px;height:251px;border-radius:18px;display:flex;align-items:flex-end;justify-content:center;padding-bottom:22px;text-align:center;color:var(--white);font-family:'Poppins',sans-serif;font-weight:700;font-size:22px;line-height:33px;text-shadow:0 2px 4px rgba(0,0,0,.5)}

.news-title{left:0;top:2190px;width:1200px;text-align:center;color:var(--slate);font-size:35px}
.news-text{left:190px;top:2258px;width:820px;text-align:center;font-size:15px;line-height:28px;color:#333}
.news-form{left:255px;top:2348px;width:690px;height:60px;border-radius:30px;background:var(--white);box-shadow:0 2px 10px rgba(0,0,0,.15);display:flex;overflow:hidden}
.news-form .field{flex:1;display:flex;align-items:center;padding-left:24px;font-size:15px;font-weight:700;color:#333}
.news-form .send{width:208px;background:var(--slate-dark);color:var(--white);display:flex;align-items:center;justify-content:center;font-family:'Poppins',sans-serif;font-weight:600;font-size:20px;border-radius:0 30px 30px 0}

.origin{left:0;top:2490px;width:1200px;height:510px}
.origin-title{left:109px;top:2550px;color:var(--white);font-size:36px}
.origin-text{left:109px;top:2606px;width:428px;color:var(--white);font-size:15px;line-height:29px;text-align:justify}
.origin-text p+p{margin-top:29px}
.btn-light{left:110px;top:2891px;width:158px;height:47px;background:var(--white);color:var(--blue-deep);font-size:16px}

.footer{left:0;top:3000px;width:1200px;height:393px;background:var(--black);color:var(--white)}
.footer-brand{left:112px;top:3090px}
.footer-brand .mark{width:60px;height:60px}
.footer-brand{font-size:22px}
.f-social{left:111px;top:3219px;display:flex;gap:26px}
.f-social span{width:32px;height:32px;border-radius:50%;background:var(--white);display:block}
.f-col h3{font-family:'Poppins',sans-serif;font-weight:600;font-size:18px;margin-bottom:14px}
.f-col li{list-style:none;font-size:15px;line-height:34px;display:flex;align-items:center;gap:10px}
.f-col li svg{width:13px;height:13px}
.f-contact li{line-height:26px;align-items:flex-start;margin-bottom:18px;gap:14px}
.f-contact .ic{width:32px;height:32px;border-radius:50%;background:var(--white);flex:none;display:flex;align-items:center;justify-content:center}
.f-contact .ic svg{width:16px;height:16px}
.f-rule{left:111px;top:3312px;width:978px;height:1px;background:#666}
.copy{left:0;top:3346px;width:1200px;text-align:center;font-family:'Poppins',sans-serif;font-weight:600;font-size:15px}
</style>
</head>
<body>

<div class="abs topbar">Call us today on +1 555 010 0199 for a free onsite quotation or email hello@kvrmaintenance.example</div>

<section class="abs hero" role="img" aria-label="Engineer in safety glasses inspecting a jet engine with a laptop"></section>
<div class="abs brand" style="left:64px;top:98px"><span class="mark"></span><span>KVR<br>Maintenance</span></div>
<nav class="abs nav"><span>HOME</span><span>ABOUT</span><span>WHAT WE DO</span><span>WHY CHOOSE US</span></nav>
<div class="abs socials"><span></span><span></span><span></span><span></span></div>
<div class="abs btn btn-contact">CONTACT US</div>
<div class="abs hero-kicker">WELCOME TO KVR MAINTENANCE</div>
<h1 class="abs head hero-title">MECHANICAL MAINTENANCE<br>BUSINESS</h1>
<p class="abs hero-text">Director of the company has over 20-year experience in the fixed and mobile plant industries ranging from Perth local and overseas.</p>
<div class="abs btn btn-start">GET STARTED</div>
<div class="abs head hero-tel">TEL: +1 555 010 0199</div>

<svg class="abs why-art" viewBox="0 0 445 468">
  <defs><linearGradient id="sunset" x1="0" y1="0" x2="0" y2="1"><stop offset="0" stop-color="#e8a23a"/><stop offset=".5" stop-color="#c9622a"/><stop offset="1" stop-color="#2f5878"/></linearGradient></defs>
  <path d="M398 62 A234 234 0 1 0 398 406 A205 205 0 1 1 398 62 Z" fill="#54575c"/>
  <circle cx="226" cy="237" r="203" fill="url(#sunset)" role="img" aria-label="Worker in orange overalls on an offshore drilling platform at sunset"/>
</svg>
<h2 class="abs head why-title">WHY CHOOSE US</h2>
<div class="abs why-text">
  <p>Nam libero tempore, cum soluta nobis est eligendi optio cumque nihil impedit quo minus id quod maxime placeat facere possimus, omnis voluptas assumenda est, omnis dolor repellendus. Temporibus autem qnecessitatibus saepe eveniet ut et voluptates repudiandae sint et molestiae non recusandae.</p>
  <p>Itaque earum rerum hic tenetur a sapiente delectus, ut aut reiciendis voluptatibus maiores alias consequatur aut perferendis doloribus asperiores repellat.</p>
</div>
<div class="abs btn btn-dark">READ MORE</div>

<svg class="abs services-band" viewBox="0 0 1200 890" preserveAspectRatio="none">
  <path d="M0 140 Q600 -110 1200 140 L1200 750 Q600 1010 0 750 Z" fill="var(--blue-soft)"/>
  <path d="M0 148 Q600 -80 1200 148 L1200 742 Q600 980 0 742 Z" fill="#1f5fb0"/>
  <rect x="0" y="180" width="1200" height="560" fill="#2a64ad" opacity=".35" role="img" aria-label="Faded earthmoving machinery on gravel"/>
</svg>
<h2 class="abs head services-title">WHAT WE DO</h2>
<div class="abs card" style="left:111px;top:1425px;background:linear-gradient(160deg,#3d5f86,#a8672a 70%,#5a4020)" role="img" aria-label="Industrial yellow pipework">Diesel Fitting</div>
<div class="abs card" style="left:444px;top:1425px;background:linear-gradient(160deg,#5d6d80,#2a3c56)" role="img" aria-label="Mechanic working on an engine">Plant Mechanics<br>Mobile</div>
<div class="abs card" style="left:776px;top:1425px;background:linear-gradient(160deg,#4a5058,#8c7440 55%,#2e3238)" role="img" aria-label="Gloved hands machining a part on a lathe">Plant Mechanics<br>Fixed</div>
<div class="abs card" style="left:111px;top:1698px;background:linear-gradient(160deg,#3a5f8f,#1d3f78)" role="img" aria-label="Blue industrial pumps in a plant">Pump Installation<br>and Repairs</div>
<div class="abs card" style="left:444px;top:1698px;background:linear-gradient(160deg,#56606c,#2c3440)" role="img" aria-label="Procurement specialist with digital interface">Procurement</div>
<div class="abs card" style="left:776px;top:1698px;background:linear-gradient(160deg,#6c7784,#2f3844)" role="img" aria-label="Team meeting at a whiteboard">Supervision and Small<br>Project Management</div>

<h2 class="abs head news-title">SIGN UP OUR NEWSLETTER</h2>
<p class="abs news-text">Nemo enim ipsam voluptatem quia voluptas sit aspernatur aut odit aut fugit, sed quia consequuntur magni dolores eos qui ratione voluptatem sequi nesciunt.</p>
<div class="abs news-form"><div class="field">Enter the Mail</div><div class="send">SUBSCRIBE</div></div>

<svg class="abs origin" viewBox="0 0 1200 510">
  <defs>
    <linearGradient id="originBlue" x1="0" y1="0" x2="1" y2="1"><stop offset="0" stop-color="var(--blue)"/><stop offset="1" stop-color="var(--blue-deep)"/></linearGradient>
    <linearGradient id="city" x1="0" y1="0" x2="0" y2="1"><stop offset="0" stop-color="#8fa4c4"/><stop offset=".45" stop-color="#d9826a"/><stop offset=".75" stop-color="#3a3f5c"/><stop offset="1" stop-color="#1f2740"/></linearGradient>
  </defs>
  <rect width="1200" height="510" fill="url(#originBlue)"/>
  <polygon points="568,0 1200,0 1200,510 632,510" fill="url(#city)" role="img" aria-label="City skyline by the river at sunset"/>
</svg>
<h2 class="abs head origin-title">WHERE WE COME FROM</h2>
<div class="abs origin-text">
  <p>Director of the company has over 20-year experience in the fixed and mobile plant industries ranging from Perth local and overseas. Facilities like precious metals refining, offshore drilling and production platform, open cut and underground mining, civils, geotechnical and construction equipment and large-scale construction as an expat overseas.</p>
  <p>We offer personalised service to all small and medium size business across a diverse range of industries.</p>
</div>
<div class="abs btn btn-light">READ MORE</div>

<footer class="abs footer"></footer>
<div class="abs brand footer-brand"><span class="mark"></span><span>KVR<br>Maintenance</span></div>
<div class="abs f-social"><span></span><span></span><span></span><span></span></div>

<div class="abs f-col" style="left:430px;top:3068px;color:#fff">
  <h3>QUICK LINKS</h3>
  <ul>
    <li><svg viewBox="0 0 12 12"><path d="M1 5h6V2l4 4-4 4V7H1z" fill="#fff"/></svg>Home</li>
    <li><svg viewBox="0 0 12 12"><path d="M1 5h6V2l4 4-4 4V7H1z" fill="#fff"/></svg>About</li>
    <li><svg viewBox="0 0 12 12"><path d="M1 5h6V2l4 4-4 4V7H1z" fill="#fff"/></svg>Services</li>
    <li><svg viewBox="0 0 12 12"><path d="M1 5h6V2l4 4-4 4V7H1z" fill="#fff"/></svg>Testimonials</li>
    <li><svg viewBox="0 0 12 12"><path d="M1 5h6V2l4 4-4 4V7H1z" fill="#fff"/></svg>Contact Us</li>
  </ul>
</div>
<div class="abs f-col" style="left:654px;top:3068px;color:#fff">
  <h3>HELP LINKS</h3>
  <ul>
    <li><svg viewBox="0 0 12 12"><path d="M1 5h6V2l4 4-4 4V7H1z" fill="#fff"/></svg>FAQ</li>
    <li><svg viewBox="0 0 12 12"><path d="M1 5h6V2l4 4-4 4V7H1z" fill="#fff"/></svg>Terms of use</li>
    <li><svg viewBox="0 0 12 12"><path d="M1 5h6V2l4 4-4 4V7H1z" fill="#fff"/></svg>Privacy Policy</li>
    <li><svg viewBox="0 0 12 12"><path d="M1 5h6V2l4 4-4 4V7H1z" fill="#fff"/></svg>Support Links</li>
    <li><svg viewBox="0 0 12 12"><path d="M1 5h6V2l4 4-4 4V7H1z" fill="#fff"/></svg>Conditions</li>
  </ul>
</div>
<div class="abs f-col f-contact" style="left:862px;top:3068px;color:#fff">
  <h3>CONTACT US</h3>
  <ul>
    <li><span class="ic"><svg viewBox="0 0 16 16"><path d="M8 1a5 5 0 0 0-5 5c0 4 5 9 5 9s5-5 5-9a5 5 0 0 0-5-5zm0 7a2 2 0 1 1 0-4 2 2 0 0 1 0 4z" fill="#000"/></svg></span><span>KVR Maintenance<br>United States</span></li>
    <li><span class="ic"><svg viewBox="0 0 16 16"><path d="M4 1l3 3-2 2c1 2 3 4 5 5l2-2 3 3-2 3C7 15 1 9 1 3z" fill="#000"/></svg></span><span style="line-height:32px">+1 555 010 0199</span></li>
    <li><span class="ic"><svg viewBox="0 0 16 16"><rect x="1" y="3" width="14" height="10" rx="1" fill="#000"/><path d="M1 4l7 5 7-5" stroke="#fff" stroke-width="1.3" fill="none"/></svg></span><span style="line-height:32px">hello@kvrmaintenance.example</span></li>
  </ul>
</div>
<div class="abs f-rule"></div>
<div class="abs copy" style="color:#fff">Copyrights@2024. KVR Maintenance.All Rights Reserved</div>

</body>
</html>
```